Executive Coaching and Spiritual Development Company needs a business card design.

We need a business card design for our company. We already have a logo that was created through Brightloom that we will submit and would like to see this work on black, blue and white backgrounds. Our personal information should be included as well. The design should communicate trust, spirituality, support and partnership.

Industry/Entity Type

Business

Colors
0255a3
33a6d7
ffffff
000000
474747

Requirements
Nice to have
• The colors offered here are just ideas--we are open to other suggestions, too.

```html
<!DOCTYPE html>
<html lang="en">
<head>
<meta charset="utf-8">
<title>Stillwater Business Card</title>
<link rel="stylesheet" href="https://fonts.googleapis.com/css2?family=Arvo:wght@400;700&family=Lato:wght@400;700;900&display=swap">
<style>
  :root {
    --backdrop: #2b2b2b;
    --brand-blue: #0f5cb8;
    --card-white: #f7f8f9;
    --ink-navy: #14202b;
    --ink-dark: #1b1b1b;
    --faint-ring: rgba(20, 32, 43, 0.08);
    --white: #ffffff;
  }
  * { box-sizing: border-box; margin: 0; padding: 0; }
  html, body { width: 1200px; height: 900px; overflow: hidden; }
  body {
    background: var(--backdrop);
    position: relative;
    font-family: "Lato", Arial, sans-serif;
  }
  .card {
    position: absolute;
    width: 560px;
    height: 320px;
    border-radius: 18px;
    background: var(--card-white);
    overflow: hidden;
    box-shadow: 0 14px 30px rgba(0,0,0,0.45);
  }
  .card-front { left: 70px; top: 70px; }
  .card-back { left: 570px; top: 500px; }

  .band {
    position: absolute;
    left: 0; right: 0;
    background: var(--brand-blue);
  }
  .card-front .band-top { top: 0; height: 58px; }
  .card-front .band-bottom { bottom: 0; height: 58px; }
  .card-back .band-top { top: 0; height: 62px; }

  .faint-ring {
    position: absolute;
    border-radius: 50%;
    border: 3px solid var(--faint-ring);
  }
  .card-front .faint-ring { width: 110px; height: 110px; right: 18px; top: 36px; }
  .card-back .faint-ring { width: 150px; height: 150px; right: 30px; top: 80px; }

  .brand {
    position: absolute;
    display: flex;
    align-items: center;
    gap: 16px;
  }
  .brand-dot {
    width: 74px; height: 74px;
    border-radius: 50%;
    border: 3px solid var(--ink-navy);
    flex: none;
  }
  .brand-name {
    font-family: "Arvo", Georgia, serif;
    font-weight: 400;
    font-size: 54px;
    color: var(--ink-navy);
    letter-spacing: 0.5px;
  }
  .card-front .brand { left: 76px; top: 118px; }
  .card-back .brand { left: 70px; top: 98px; }

  .website {
    position: absolute;
    right: 34px;
    bottom: 20px;
    color: var(--white);
    font-size: 15px;
    font-weight: 700;
    letter-spacing: 2.5px;
  }

  .holder {
    position: absolute;
    right: 26px;
    top: 12px;
    text-align: right;
    color: var(--white);
    line-height: 1;
  }
  .holder-name { font-weight: 900; font-size: 22px; letter-spacing: 0.5px; }
  .holder-role { font-size: 11px; font-weight: 700; letter-spacing: 1px; margin-top: 3px; }

  .contacts {
    position: absolute;
    left: 168px;
    top: 196px;
    display: grid;
    grid-template-columns: 190px auto;
    row-gap: 6px;
    column-gap: 10px;
    font-size: 15px;
    font-weight: 700;
    color: var(--ink-dark);
  }
  .contact { display: flex; align-items: center; gap: 8px; }
  .contact svg { width: 14px; height: 14px; fill: var(--ink-dark); flex: none; }
  .address {
    position: absolute;
    left: 24px;
    bottom: 26px;
    font-size: 15px;
    font-weight: 700;
    color: var(--ink-dark);
    display: flex; align-items: center; gap: 10px;
  }
  .address svg { width: 16px; height: 16px; fill: var(--ink-dark); }
</style>
</head>
<body>

<section class="card card-front" aria-label="Card front">
  <div class="band band-top"></div>
  <div class="faint-ring"></div>
  <div class="brand">
    <span class="brand-dot"></span>
    <span class="brand-name">Stillwater</span>
  </div>
  <div class="band band-bottom"></div>
  <p class="website">www.@stillwater.ca</p>
</section>

<section class="card card-back" aria-label="Card back">
  <div class="band band-top"></div>
  <div class="holder">
    <p class="holder-name">YOUR NAME</p>
    <p class="holder-role">DIRECTOR</p>
  </div>
  <div class="faint-ring"></div>
  <div class="brand">
    <span class="brand-dot"></span>
    <span class="brand-name">Stillwater</span>
  </div>

  <div class="contacts">
    <span class="contact">
      <svg viewBox="0 0 16 16" aria-hidden="true"><path d="M1 5c0-2 3-3 7-3s7 1 7 3v1h-4V4.5H5V6H1zM3 7h10l1 7H2z"/></svg>
      514-555-0148
    </span>
    <span class="contact">
      <svg viewBox="0 0 16 16" aria-hidden="true"><path d="M4 1h8v4H4zM1 6h14v6h-3v3H4v-3H1zM5 10v4h6v-4z"/></svg>
      +65 6000 3390
    </span>
    <span class="contact">
      <svg viewBox="0 0 16 16" aria-hidden="true"><path d="M4 0h8a1 1 0 0 1 1 1v14a1 1 0 0 1-1 1H4a1 1 0 0 1-1-1V1a1 1 0 0 1 1-1zm1 2v11h6V2z"/></svg>
      +65 9000 4172
    </span>
    <span class="contact">
      <svg viewBox="0 0 16 16" aria-hidden="true"><path d="M0 3h16v10H0zM1.5 4.5 8 9l6.5-4.5v7h-13z"/></svg>
      info@stillwater.ca
    </span>
  </div>

  <p class="address">
    <svg viewBox="0 0 16 16" aria-hidden="true"><path d="M8 1l8 7h-2.5v7h-4v-5h-3v5h-4V8H0z"/></svg>
    48 Harbour Lane Business Park 3B #05-21 Northgate Hub Singapore 560000
  </p>
</section>

</body>
</html>
```